Workfold Background Picture

Job Title:
Professional WorkFold Banner Design for Individual in Architectural Industry

Description:

Hello talented designers,

I am looking for a creative and professional graphic designer to create a WorkFold banner for my personal profile. I am deeply involved in the architectural systems industry, specializing in innovative and sustainable building solutions.

What I'm Looking For:

Personal Branding: The banner should reflect my professional identity and role in the architectural systems industry. It should be more personal than corporate.

Visual Elements: Include imagery or abstract designs that represent architecture, innovation, and sustainability. The design should subtly hint at my industry expertise and areas of specialization.

Professional and Engaging: The design should be visually striking but maintain a professional look. It should engage viewers and encourage them to learn more about my professional background and skills.

File Requirements: The final design should be provided in a high-resolution JPEG or PNG format, fitting WorkFold's banner dimensions.

To Apply, Please Provide:

A summary of your design experience, especially with WorkFold banners or personal branding projects.
A portfolio showcasing your previous work, highlighting any designs related to personal branding or professional themes.
Your estimated timeline and budget for the project.
Selection Criteria:

Creativity in reflecting a personal professional brand.
Experience with individual professional branding.
Quality and relevance of the portfolio.
Competitive pricing and clear communication.
I am excited to see your creative approaches and look forward to collaborating to craft a banner that perfectly encapsulates my professional persona on WorkFold.

Thank you!

My workfold page:
workfold.com/in/dervomakti

Our website:

https://files.trovamesh.net/share/folders/7bQkT2wXpLm9RzV4nHcJ8sFd3aYeUo6Ni?usp=share_link

Some photos of our projects:

```html
<!DOCTYPE html>
<html lang="en">
<head>
<meta charset="utf-8">
<title>Dervo Makti – Profile Banner</title>
<link rel="stylesheet" href="https://fonts.googleapis.com/css2?family=Allura&family=Montserrat:wght@400;600&family=Poppins:wght@500&display=swap">
<style>
  :root{
    --page:#f1f0ed;
    --banner-deep:#36588b;
    --banner-mid:#4568a0;
    --ink:#ffffff;
    --ink-soft:#e6edf7;
    --accent:#5fc3f0;
    --hex-line:#a9c2e4;
    --sky-light:#c7d8ec;
    --sky-mid:#8aa7cf;
    --facade:#3e64aa;
    --interior:#cfc6b8;
  }
  *{margin:0;padding:0;box-sizing:border-box}
  html,body{width:1200px;height:1200px;overflow:hidden;background:var(--page)}
  .banner{
    position:absolute;left:50px;top:462px;width:1100px;height:275px;overflow:hidden;
    background:linear-gradient(100deg,var(--banner-deep) 0%,var(--banner-mid) 55%,var(--banner-deep) 100%);
  }
  .banner__texture{position:absolute;inset:0;
    background:linear-gradient(180deg,rgba(255,255,255,.04),rgba(0,0,0,.08))}
  .brand{position:absolute;left:27px;top:30px;display:flex;align-items:center;gap:8px;
    font-family:"Montserrat",sans-serif;font-weight:600;font-size:17px;letter-spacing:5px;color:var(--ink)}
  .brand__square{width:12px;height:12px;background:var(--ink)}
  .brand__sub{position:absolute;left:27px;top:56px;font-family:"Montserrat",sans-serif;font-weight:600;
    font-size:6px;letter-spacing:2px;color:var(--ink)}
  .intro{position:absolute;left:316px;top:50px;width:300px;color:var(--ink)}
  .intro__name{font-family:"Allura",cursive;font-size:56px;line-height:56px;color:var(--ink);padding-left:3px}
  .intro__role{font-family:"Poppins",sans-serif;font-weight:500;font-size:17.5px;line-height:24px;margin-top:-2px}
  .intro__lines{font-family:"Montserrat",sans-serif;font-size:12.6px;line-height:14.6px;margin-top:1px;
    padding-left:4px;color:var(--ink-soft);letter-spacing:.2px}
  .socials{display:flex;gap:11px;margin-top:12px;padding-left:2px;list-style:none;white-space:nowrap;
    font-family:"Montserrat",sans-serif;font-weight:600;font-size:5.6px;letter-spacing:.2px}
  .socials li{display:flex;align-items:center;gap:3px}
  .socials li::before{content:"";width:5px;height:5px;border-radius:1px;background:var(--accent)}
  .collage{position:absolute;left:0;top:0}
</style>
</head>
<body>
  <section class="banner" aria-label="Profile banner">
    <div class="banner__texture" role="img" aria-label="Faint photo of a residential tower facade"></div>

    <div class="brand"><span class="brand__square"></span>KORVANE</div>
    <div class="brand__sub">BUILDING SYSTEMS</div>

    <svg class="collage" width="1100" height="275" viewBox="0 0 1100 275">
      <defs>
        <linearGradient id="sky" x1="0" y1="0" x2="0" y2="1">
          <stop offset="0" stop-color="var(--sky-light)"/><stop offset="1" stop-color="var(--sky-mid)"/>
        </linearGradient>
        <linearGradient id="facade" x1="0" y1="0" x2="1" y2="1">
          <stop offset="0" stop-color="#5a80c0"/><stop offset="1" stop-color="var(--facade)"/>
        </linearGradient>
        <linearGradient id="room" x1="0" y1="0" x2="0" y2="1">
          <stop offset="0" stop-color="#d9dde2"/><stop offset="1" stop-color="var(--interior)"/>
        </linearGradient>
      </defs>
      <g fill="none" stroke="var(--hex-line)" stroke-width="1" opacity=".7">
        <polygon points="660,-4 674,4 674,20 660,28 646,20 646,4"/>
        <polygon points="708,170 768,205 768,275 708,310 648,275 648,205"/>
        <polyline points="1062,170 1090,155 1090,275"/>
      </g>
      <g role="img" aria-label="Honeycomb collage of project photos: balconies, city views, bright interiors and blue residential towers">
        <polygon fill="url(#facade)" points="846,-113 913.5,-74 913.5,4 846,43 778.5,4 778.5,-74"/>
        <polygon fill="url(#facade)" points="995,-113 1062.5,-74 1062.5,4 995,43 927.5,4 927.5,-74"/>
        <polygon fill="url(#sky)" points="772,28 839.5,67 839.5,145 772,184 704.5,145 704.5,67"/>
        <polygon fill="url(#room)" points="921,22 988.5,61 988.5,139 921,178 853.5,139 853.5,61"/>
        <polygon fill="url(#facade)" points="1070,22 1137.5,61 1137.5,139 1070,178 1002.5,139 1002.5,61"/>
        <polygon fill="url(#facade)" points="846,158 913.5,197 913.5,275 846,314 778.5,275 778.5,197"/>
        <polygon fill="url(#facade)" points="995,158 1062.5,197 1062.5,275 995,314 927.5,275 927.5,197"/>
        <polygon fill="url(#room)" points="708,185 755.6,212.5 755.6,267.5 708,295 660.4,267.5 660.4,212.5"/>
        <polygon fill="url(#room)" points="700,94 723.4,107.5 723.4,134.5 700,148 676.6,134.5 676.6,107.5"/>
        <polygon fill="url(#room)" points="712,155 723.3,161.5 723.3,174.5 712,181 700.7,174.5 700.7,161.5"/>
      </g>
      <polygon fill="#8fb0e0" points="1087,0 1100,0 1100,15 1087,22 1074,15 1074,0"/>
    </svg>

    <div class="intro">
      <div class="intro__name">Dervo Makti</div>
      <div class="intro__role">Founder at KorvaneSystems.com</div>
      <div class="intro__lines">
        Green Building Technologies Innovator |<br>
        15+ Years Work Experience |<br>
        BCom. at University of Halvern |<br>
        Contact Me For Green Buildings Soulutions
      </div>
      <ul class="socials">
        <li>WW.KORVANE.COM</li>
        <li>FRIENDLOOP</li>
        <li>SNAPFRAME</li>
        <li>FRIENDLOOP</li>
        <li>VIEWTUBE</li>
      </ul>
    </div>
  </section>
</body>
</html>
```